SOLVE Study flyer

I need help designing a flyer for a research study that will include brain imaging in adolescents. The info is in the attached document. The study is called the Sequoia Outlook Lantern Valley Echo (SOLVE) study. Ideally this would be returned as a document that I can edit in the future as we will have several new recruitment phases (different age groups, etc. I also would love to have a logo designed as part of this project, but I recognize that might be a separate design request.

```html
<!DOCTYPE html>
<html lang="en">
<head>
<meta charset="utf-8">
<title>SOLVE Study Flyer</title>
<link rel="stylesheet" href="https://fonts.googleapis.com/css2?family=Anton&family=Poppins:wght@400;500;600;700;800&display=swap">
<style>
  :root {
    --navy: #13318f;
    --ink: #2b2b2b;
    --yellow: #fdb51b;
    --red: #c8101e;
    --white: #ffffff;
    --photo-grey: #b9b6ae;
    --photo-warm: #d8d2c4;
  }
  * { box-sizing: border-box; margin: 0; padding: 0; }
  html, body { width: 1008px; height: 1200px; overflow: hidden; }
  body { position: relative; background: var(--white); font-family: "Poppins", sans-serif; color: var(--ink); }
  .corner-arc { position: absolute; left: 0; top: 0; width: 1008px; height: 1200px; pointer-events: none; }
  .title { position: absolute; left: 72px; top: 78px; font-size: 50px; font-weight: 600; color: var(--navy); letter-spacing: -0.5px; }
  .question { position: absolute; left: 72px; top: 152px; font-size: 37px; font-weight: 600; line-height: 43px; color: var(--ink); }
  .age-range { position: absolute; left: 68px; top: 232px; font-family: "Anton", sans-serif; font-size: 152px; line-height: 160px; color: var(--yellow); letter-spacing: 2px; }
  .worry-box { position: absolute; left: 71px; top: 392px; width: 399px; height: 73px; background: var(--navy); color: var(--white); padding: 5px 0 0 20px; font-size: 24px; line-height: 30px; font-weight: 400; }
  .worry-box strong { font-weight: 700; }
  .intro { position: absolute; left: 72px; top: 482px; width: 390px; font-size: 14.5px; line-height: 17.5px; color: var(--ink); }
  .hero-photo { position: absolute; left: 500px; top: 83px; width: 455px; height: 463px; border: 4px solid var(--white); border-top-right-radius: 112px; background: radial-gradient(circle at 55% 60%, #c59a7e 0 18%, transparent 19%), linear-gradient(160deg, var(--photo-warm), var(--photo-grey) 55%, #8d8a84); }
  .pill { position: absolute; top: 605px; height: 62px; border: 2px solid var(--navy); border-radius: 31px; display: flex; align-items: center; padding-left: 4px; }
  .pill--study { left: 71px; width: 395px; }
  .pill--eligible { left: 559px; width: 373px; }
  .pill-icon { width: 54px; height: 54px; flex: none; }
  .pill-text { margin-left: 12px; font-size: 26px; line-height: 26px; font-weight: 600; color: var(--navy); }
  .pill-text b { color: var(--ink); font-weight: 700; }
  .pill-text span { font-weight: 500; }
  .divider { position: absolute; left: 520px; top: 600px; width: 1px; height: 215px; background: #d5d5d5; }
  .checklist { position: absolute; list-style: none; font-size: 15.5px; line-height: 17px; font-weight: 500; color: var(--ink); }
  .checklist--study { left: 74px; top: 675px; width: 400px; }
  .checklist--eligible { left: 562px; top: 671px; width: 380px; }
  .checklist li { position: relative; padding-left: 20px; margin-bottom: 15px; }
  .checklist li::before { content: ""; position: absolute; left: 0; top: 3px; width: 11px; height: 11px; border-radius: 50%; background: var(--navy); }
  .checklist li::after { content: ""; position: absolute; left: 3.3px; top: 5.5px; width: 4px; height: 2px; border-left: 1.5px solid var(--white); border-bottom: 1.5px solid var(--white); transform: rotate(-45deg); }
  .family-photo { position: absolute; left: 89px; top: 835px; width: 548px; height: 212px; border-radius: 60px 60px 0 0; background: linear-gradient(180deg, #f1ede8 0%, #d9ccbf 45%, #9fb3c8 100%); }
  .badge { position: absolute; left: 665px; top: 812px; width: 230px; height: 230px; }
  .badge-text { position: absolute; left: 665px; top: 872px; width: 230px; text-align: center; color: var(--white); }
  .badge-label { font-size: 17px; line-height: 19px; font-weight: 500; }
  .badge-amount { font-size: 58px; line-height: 70px; font-weight: 800; letter-spacing: -1px; }
  .badge-amount sup { font-size: 32px; vertical-align: 18px; margin-right: 2px; }
  .cta-bar { position: absolute; left: 63px; top: 1047px; width: 895px; height: 57px; display: flex; border-radius: 28px; overflow: hidden; font-size: 27px; font-weight: 700; }
  .cta-info { width: 432px; background: var(--yellow); color: #1d1d1d; padding: 7px 0 0 25px; }
  .cta-join { flex: 1; background: var(--navy); color: var(--white); padding: 7px 0 0 16px; }
  .contact { position: absolute; left: 81px; top: 1104px; display: flex; align-items: center; white-space: nowrap; }
  .contact-lead { font-size: 44px; color: var(--navy); font-weight: 400; }
  .contact-lead strong { font-weight: 700; }
  .contact-mail { display: flex; align-items: center; margin-left: 14px; font-size: 28px; color: #1d1d1d; }
  .contact-mail svg { width: 26px; height: 26px; margin-right: 8px; }
</style>
</head>
<body>
  <svg class="corner-arc" viewBox="0 0 1008 1200" aria-hidden="true">
    <circle cx="800" cy="200" r="280" fill="var(--navy)"/>
  </svg>

  <h1 class="title">SOLVE Study</h1>
  <p class="question">Are you the parent<br>of a child age</p>
  <p class="age-range">10-17?</p>
  <div class="worry-box">Do they worry or <strong>overthink</strong><br><strong>negative emotions?</strong></div>
  <p class="intro">Northbrook University researchers are seeking girls age 10-17 for a study about brain activity in emotions and decision-making and how they relate to puberty, anxiety and depression.</p>

  <div class="hero-photo" role="img" aria-label="Photo of a teenager scratching his head with sketched tangled lines and question marks around him"></div>

  <div class="pill pill--study">
    <svg class="pill-icon" viewBox="0 0 54 54" aria-hidden="true">
      <circle cx="27" cy="27" r="27" fill="var(--navy)"/>
      <path d="M16 38 V22 a2 2 0 0 1 4 0 V28 M20 26 V17 a2 2 0 0 1 4 0 V27 M24 18 a2 2 0 0 1 4 0 V28 M28 20 a2 2 0 0 1 4 0 V32 c0 5 -3 8 -8 8 h-3 c-3 0 -5 -2 -5 -2" fill="none" stroke="var(--white)" stroke-width="2" stroke-linecap="round"/>
      <path d="M34 30 l4 -6 a2 2 0 0 1 3 2 l-2 6 V40" fill="none" stroke="var(--white)" stroke-width="2" stroke-linecap="round"/>
    </svg>
    <p class="pill-text"><b>Study</b> participation<br><span>involves</span></p>
  </div>

  <div class="divider"></div>

  <div class="pill pill--eligible">
    <svg class="pill-icon" viewBox="0 0 54 54" aria-hidden="true">
      <circle cx="27" cy="27" r="27" fill="var(--navy)"/>
      <rect x="16" y="13" width="20" height="27" rx="2" fill="none" stroke="var(--white)" stroke-width="2"/>
      <path d="M19 18 l2 2 l4 -4" fill="none" stroke="var(--white)" stroke-width="2"/>
      <path d="M19 25 h12 M19 29 h12 M19 33 h8" stroke="var(--white)" stroke-width="2"/>
      <rect x="37" y="18" width="3" height="18" fill="var(--white)"/>
    </svg>
    <p class="pill-text"><b>Your child</b> <span>may be</span><br>eligible if they</p>
  </div>

  <ul class="checklist checklist--study">
    <li>One one-hour interview (online or in-person) where your child will discuss their thoughts</li>
    <li>Online questionnaires (parent and child)</li>
    <li>One two-hour visit where your child will complete an MRI scan, answer questions about their puberty stage, and have a small hair sample taken to study</li>
  </ul>

  <ul class="checklist checklist--eligible">
    <li>Are age 10-17</li>
    <li>Tend to worry or overthink<br>negative thoughts</li>
    <li>have not been diagnosed with<br>psychosis, learning problems, or autism</li>
  </ul>

  <div class="family-photo" role="img" aria-label="Photo of a mother and father comforting their young daughter on a sofa"></div>

  <svg class="badge" viewBox="-115 -115 230 230" aria-hidden="true">
    <polygon fill="var(--red)" stroke="var(--white)" stroke-width="3" points="110,0 94.2,18.7 101.6,42.1 79.8,53.4 77.8,77.8 53.4,79.8 42.1,101.6 18.7,94.2 0,110 -18.7,94.2 -42.1,101.6 -53.4,79.8 -77.8,77.8 -79.8,53.4 -101.6,42.1 -94.2,18.7 -110,0 -94.2,-18.7 -101.6,-42.1 -79.8,-53.4 -77.8,-77.8 -53.4,-79.8 -42.1,-101.6 -18.7,-94.2 0,-110 18.7,-94.2 42.1,-101.6 53.4,-79.8 77.8,-77.8 79.8,-53.4 101.6,-42.1 94.2,-18.7"/>
    <polygon fill="none" stroke="var(--white)" stroke-width="2" transform="scale(0.88)" points="110,0 94.2,18.7 101.6,42.1 79.8,53.4 77.8,77.8 53.4,79.8 42.1,101.6 18.7,94.2 0,110 -18.7,94.2 -42.1,101.6 -53.4,79.8 -77.8,77.8 -79.8,53.4 -101.6,42.1 -94.2,18.7 -110,0 -94.2,-18.7 -101.6,-42.1 -79.8,-53.4 -77.8,-77.8 -53.4,-79.8 -42.1,-101.6 -18.7,-94.2 0,-110 18.7,-94.2 42.1,-101.6 53.4,-79.8 77.8,-77.8 79.8,-53.4 101.6,-42.1 94.2,-18.7"/>
  </svg>
  <div class="badge-text">
    <p class="badge-label">Compensation<br>up to</p>
    <p class="badge-amount"><sup>$</sup>140</p>
  </div>

  <div class="cta-bar">
    <div class="cta-info">Want more information?</div>
    <div class="cta-join">Interested in participating?</div>
  </div>

  <div class="contact">
    <p class="contact-lead">Please <strong>contact us!</strong></p>
    <p class="contact-mail">
      <svg viewBox="0 0 28 28" aria-hidden="true">
        <circle cx="14" cy="14" r="14" fill="var(--yellow)"/>
        <rect x="7" y="9" width="14" height="10" rx="1" fill="#1d1d1d"/>
        <path d="M7.5 9.5 L14 15 L20.5 9.5" fill="none" stroke="var(--yellow)" stroke-width="1.4"/>
      </svg>
      solvestudy@northbrook.edu
    </p>
  </div>
</body>
</html>
```